All-Natural Head Lice Removal company

I need a business card with my pre-existing logo. We are a new company located in Portland Oregon that goes into peoples homes to help with head lice removal. My products and approach are all- natural and also will be around children.On my current logo we used Teal Bl and the color Green. I am open to new ideas just want it simple and creative

Target Market(s)

my biggest market is families of school aged children

Industry/Entity Type

Business

Contact Information for Business Card

see upload for details from previous business card

Font styles to use
Serif

Colors
33a6d7
9bcb3b
f37122

Requirements
Must have
• Basic information/ logo put into a creative format that is catching to the eye
Nice to have
• creative

```html
<!DOCTYPE html>
<html lang="en">
<head>
<meta charset="utf-8">
<title>Clear Crown – Business Card</title>
<link rel="stylesheet" href="https://fonts.googleapis.com/css2?family=Arvo:wght@400;700&display=swap">
<style>
  :root {
    --bg: #ecebe7;
    --green-light: #a6da6a;
    --green: #79c043;
    --green-deep: #5faa2c;
    --blue-light: #8fd2f0;
    --blue: #33a6d7;
    --blue-deep: #2288c2;
    --ink: #1c1c1c;
    --white: #ffffff;
    --shadow: rgba(0,0,0,.22);
  }
  * { box-sizing: border-box; margin: 0; padding: 0; }
  html, body { width: 1200px; height: 913px; overflow: hidden; }
  body {
    background: var(--bg);
    font-family: "Arvo", Georgia, serif;
    position: relative;
  }
  .card {
    position: absolute;
    width: 560px;
    height: 320px;
    border-radius: 18px;
    overflow: hidden;
    box-shadow: 0 10px 28px var(--shadow);
    color: var(--white);
  }
  .card--front {
    left: 50px; top: 120px;
    background: linear-gradient(160deg, var(--green-light) 0%, var(--green) 45%, var(--green-deep) 100%);
  }
  .card--back {
    left: 590px; top: 470px;
    background: linear-gradient(200deg, var(--blue-light) 0%, var(--blue) 50%, var(--blue-deep) 100%);
  }
  .card__base { position: absolute; inset: 0; width: 100%; height: 100%; }

  .brand {
    position: absolute;
    display: flex;
    align-items: center;
    gap: 10px;
    font-weight: 700;
    color: var(--ink);
  }
  .brand__dot {
    width: 46px; height: 46px;
    border-radius: 50%;
    background: var(--white);
    flex: none;
  }
  .brand__name { font-size: 30px; line-height: 1; }
  .card--front .brand { left: 30px; top: 96px; }
  .card--back .brand { right: 40px; top: 62px; }
  .card--back .brand__dot { background: var(--green); }
  .card--back .brand__name { font-size: 36px; }

  .tagline {
    position: absolute;
    font-size: 14px;
    letter-spacing: .2px;
  }
  .card--front .tagline { left: 30px; top: 40px; }

  .person {
    position: absolute;
    right: 36px; top: 92px;
    text-align: right;
  }
  .person__name {
    font-size: 17px;
    font-weight: 700;
    letter-spacing: .5px;
    padding-bottom: 4px;
    border-bottom: 1px solid rgba(255,255,255,.85);
  }
  .person__role {
    font-size: 10px;
    letter-spacing: 1px;
    color: var(--ink);
    margin-top: 3px;
  }

  .divider {
    position: absolute;
    left: 30px; right: 30px; top: 178px;
    height: 1px;
    background: rgba(255,255,255,.85);
  }

  .contact {
    position: absolute;
    left: 30px; top: 196px;
    list-style: none;
    font-size: 13px;
    line-height: 21px;
  }
  .contact li { display: flex; align-items: center; gap: 9px; }
  .contact svg { width: 12px; height: 12px; fill: var(--ink); flex: none; }

  .promo {
    position: absolute;
    left: 30px; top: 206px;
    font-size: 14px;
    line-height: 20px;
  }
  .web {
    position: absolute;
    left: 40px; bottom: 16px;
    font-size: 13px;
    letter-spacing: .3px;
  }
</style>
</head>
<body>

  <section class="card card--front" aria-label="Business card front">
    <svg class="card__base" viewBox="0 0 560 320" preserveAspectRatio="none" aria-hidden="true">
      <path d="M0,284 H560 V320 H0 Z" fill="#1c1c1c"/>
      <path d="M392,320 V262 Q392,226 430,226 H560 V320 Z" fill="#ffffff"/>
    </svg>
    <p class="tagline">All Natural In-Home Lice Removal Services</p>
    <div class="brand">
      <span class="brand__dot"></span>
      <span class="brand__name">Clear Crown</span>
    </div>
    <div class="person">
      <p class="person__name">DANA WHITFIELD</p>
      <p class="person__role">OWNER</p>
    </div>
    <div class="divider"></div>
    <ul class="contact">
      <li>
        <svg viewBox="0 0 24 24"><path d="M6.6 10.8a15.1 15.1 0 0 0 6.6 6.6l2.2-2.2a1 1 0 0 1 1-.25 11.4 11.4 0 0 0 3.6.57 1 1 0 0 1 1 1V20a1 1 0 0 1-1 1A17 17 0 0 1 3 4a1 1 0 0 1 1-1h3.5a1 1 0 0 1 1 1c0 1.25.2 2.45.57 3.57a1 1 0 0 1-.25 1z"/></svg>
        1-855-555-NITS (6487)
      </li>
      <li>
        <svg viewBox="0 0 24 24"><path d="M2 5h20v14H2z M4 7v.5l8 5 8-5V7z" fill-rule="evenodd"/></svg>
        Dana@ClearCrown.com
      </li>
      <li>
        <svg viewBox="0 0 24 24"><circle cx="12" cy="12" r="10"/></svg>
        www.ClearCrown.com
      </li>
    </ul>
  </section>

  <section class="card card--back" aria-label="Business card back">
    <svg class="card__base" viewBox="0 0 560 320" preserveAspectRatio="none" aria-hidden="true">
      <path d="M0,320 V300 Q0,262 60,262 H560 V320 Z" fill="#ffffff"/>
      <path d="M0,320 V274 H190 Q240,274 256,300 Q268,320 300,320 Z" fill="#1c1c1c"/>
      <path d="M0,274 H190 Q240,274 256,300 Q268,320 300,320 H0 Z" fill="#1c1c1c"/>
    </svg>
    <div class="brand">
      <span class="brand__dot"></span>
      <span class="brand__name">Clear Crown</span>
    </div>
    <p class="promo">Try Clear Crown Today and Be Lice Free Tomorrow!<br>All Natural In-Home Lice Removal Services</p>
    <p class="web">www.ClearCrown.com</p>
  </section>

</body>
</html>
```